Book Cover for a Short Story called “Leaving Harbor"

Pretty Straightforward. Looking for a 5.5X8.5 book cover. The story is a very short (40 pages) story about a man who moves from Greece to Canada in 1920. I have three photos to provide. One is the house that he left in greece. THen I have photos of him and his wife who he met in Toronto. I think I want the house photo on the front...
I will need cover for paper back and e-book. The ISBN numbers are:

ISBN: 978-1-5523094-2-7 (e-book)
ISBN: 978-1-5523094-1-0 (paperback)

If you want you can read it at https://kevinmarlow.example/fiction/leaving-harbor/

Colors
0094D4
00A9DD
6FCCEA
C7EBF8
E9F6FB

Requirements
Must have
• Room for a blurb about the book on the back cover. ISBN Number

```html
<!DOCTYPE html>
<html lang="en">
<head>
<meta charset="utf-8">
<title>Leaving Harbor — Cover Spread</title>
<link rel="stylesheet" href="https://fonts.googleapis.com/css2?family=Cormorant+Garamond:ital,wght@0,500;1,500&family=Open+Sans:wght@400;700&display=swap">
<style>
  :root {
    --stage: #4b4b4b;
    --paper: #ffffff;
    --ink: #111111;
    --ink-soft: #6b6b6b;
    --body: #2a2a2a;
    --photo-light: #bdbdbd;
    --photo-mid: #8c8c8c;
    --photo-dark: #4e4e4e;
    --portrait-suit: #2c3a5c;
    --portrait-skin: #d9a48e;
  }
  * { margin: 0; padding: 0; box-sizing: border-box; }
  html, body {
    width: 1200px; height: 761px; overflow: hidden;
    background: var(--stage);
  }
  .spread {
    position: absolute; left: 156px; top: 38px;
    width: 888px; height: 684px;
    background: var(--paper);
    display: flex;
  }
  .back-cover, .front-cover { position: relative; height: 100%; }
  .back-cover { width: 447px; }
  .front-cover { width: 441px; }

  .title {
    position: absolute; left: 0; right: 0;
    text-align: center;
    font-family: "Cormorant Garamond", Georgia, serif;
    font-style: italic; font-weight: 500;
    letter-spacing: 0.12em;
    color: var(--ink);
    white-space: nowrap;
  }
  .title .title-accent { color: var(--ink-soft); }
  .back-cover .title { top: 76px; font-size: 43px; }
  .front-cover .title { top: 460px; font-size: 52px; }

  .blurb {
    position: absolute;
    font-family: "Open Sans", Arial, sans-serif;
    font-size: 9.1px; line-height: 14.2px;
    color: var(--body);
    text-align: justify;
  }
  .blurb-lead { left: 45px; top: 132px; width: 360px; }
  .blurb-side { left: 208px; top: 302px; width: 197px; }
  .blurb-side p + p { margin-top: 14.2px; }

  .author-portrait {
    position: absolute; left: 9px; top: 291px;
    width: 200px; height: 298px;
    background:
      radial-gradient(ellipse 28% 20% at 50% 24%, var(--portrait-skin) 0 60%, transparent 100%),
      radial-gradient(ellipse 60% 46% at 45% 68%, var(--portrait-suit) 0 55%, transparent 100%);
    -webkit-mask-image: linear-gradient(to bottom, #000 65%, transparent 100%);
    mask-image: linear-gradient(to bottom, #000 65%, transparent 100%);
  }

  .isbn {
    position: absolute; left: 32px; top: 626px;
    font-family: "Open Sans", Arial, sans-serif;
    font-weight: 700; font-size: 8.6px;
    color: var(--ink);
  }

  .cover-photo {
    position: absolute; left: 0; top: 0;
    width: 441px; height: 372px;
    display: block;
  }

  .author-name {
    position: absolute; left: 0; right: 0; top: 614px;
    text-align: center;
    font-family: "Cormorant Garamond", Georgia, serif;
    font-weight: 500; font-size: 22px;
    letter-spacing: 0.14em;
    color: var(--ink);
  }
</style>
</head>
<body>
  <main class="spread">
    <section class="back-cover">
      <h2 class="title">Coming <span class="title-accent">Harbor</span></h2>
      <div class="blurb blurb-lead">
        <p>Lorem ipsum dolor sit amet, consectetur adipiscing elit, sed do eiusmod tempor incididunt ut labore et dolore magna aliqua. Quis ipsum suspendisse ultrices gravida. Risus commodo viverra maecenas accumsan lacus vel facilisis. Lorem ipsum dolor sit amet, consectetur adipiscing elit, sed do eiusmod tempor incididunt ut labore et dolore magna aliqua.</p>
        <p>Quis ipsum suspendisse ultrices gravida. Risus commodo viverra maecenas accumsan lacus vel facilisis. Lorem ipsum dolor sit amet, consectetur adipiscing elit, sed do eiusmod tempor incididunt ut labore et dolore magna aliqua. Quis ipsum suspendisse ultrices gravida. Risus commodo viverra maecenas accumsan lacus vel facilisis.</p>
      </div>
      <div class="author-portrait" role="img" aria-label="Portrait of the author in a navy blazer, arms crossed"></div>
      <div class="blurb blurb-side">
        <p>Quis ipsum suspendisse ultrices gravida. Risus commodo viverra maecenas accumsan lacus vel facilisis. Lorem ipsum dolor sit amet, consectetur adipiscing elit, sed do eiusmod tempor incididunt ut labore et dolore magna aliqua. Quis ipsum suspendisse ultrices gravida. Risus commodo viverra maecenas accumsan lacus vel facilisis.</p>
        <p>Quis ipsum suspendisse ultrices gravida. Risus commodo viverra maecenas accumsan lacus vel facilisis. Lorem ipsum dolor sit amet, consectetur adipiscing elit, sed do eiusmod tempor incididunt ut labore et dolore magna aliqua. Quis ipsum suspendisse ultrices gravida. Risus commodo viverra maecenas accumsan lacus vel facilisis.</p>
      </div>
      <p class="isbn">ISBN: 978-1-5523094-1-0</p>
    </section>

    <section class="front-cover">
      <svg class="cover-photo" viewBox="0 0 441 372" role="img" aria-label="Black and white photograph of an old stone house in a Greek village with a tiled roof and rubble wall">
        <defs>
          <linearGradient id="houseTones" x1="0" y1="0" x2="0" y2="1">
            <stop offset="0" stop-color="var(--photo-light)"/>
            <stop offset="0.35" stop-color="#a6a6a6"/>
            <stop offset="0.65" stop-color="var(--photo-mid)"/>
            <stop offset="1" stop-color="var(--photo-dark)"/>
          </linearGradient>
        </defs>
        <path fill="url(#houseTones)" d="M0 0H441V350L430 348 418 352 404 349 392 355 378 352 366 358 350 355 338 360 322 357 310 362 296 359 282 364 268 361 254 366 240 362 226 368 214 364 200 369 186 365 172 370 160 366 146 371 134 366 120 369 106 363 94 366 82 360 70 362 58 356 46 358 34 352 22 354 10 349 0 352Z"/>
      </svg>
      <h1 class="title">Leaving <span class="title-accent">Harbor</span></h1>
      <p class="author-name">Kevin Marlow</p>
    </section>
  </main>
</body>
</html>
```